Varnel Corporate Website for technological company

We need a modern website to promote our product and services.
You can found the actually website at the address: www.varnel-example.ch

We are a new company for B2B market. We would like do show our high precision and innovation capability.

we need a section were is possible to easily upload "news" and documents for our customers.

Target Market(s)

B2B services in the industry market

Industry/Entity Type

It Company

Coding

Coded - Design and coding required

Number of Pages Required

5+ page

Font styles to use
Other font styles liked:
• We accept propositions

Requirements
Must have
• Easy to maintain
• Presentation of the Varnel company
• Presentation of Varnel services and products
• The customer can download our ducumentation
Nice to have
• Sexy and modern

```html
<!DOCTYPE html>
<html lang="en">
<head>
<meta charset="utf-8">
<title>Varnel – Simulation and Modeling</title>
<link href="https://fonts.googleapis.com/css2?family=Raleway:wght@500;600;700;800&family=Open+Sans:ital,wght@0,400;0,600;1,400&display=swap" rel="stylesheet">
<style>
:root{
  --gold:#a99a5c;
  --gold-dark:#978850;
  --ink:#222;
  --text:#555;
  --light:#f4f5f7;
  --circle:#e9e9e9;
  --dark:#1c1c1c;
  --white:#fff;
}
*{margin:0;padding:0;box-sizing:border-box}
html,body{width:1200px;height:2643px;overflow:hidden;background:var(--white)}
body{position:relative;font-family:"Open Sans",Arial,sans-serif;color:var(--text)}
.abs{position:absolute}

/* header */
.site-header{left:0;top:0;width:1200px;height:67px;background:var(--white)}
.brand{left:162px;top:19px;font:800 28px/1 "Raleway",sans-serif;color:var(--ink);letter-spacing:1px;display:flex;align-items:center;gap:8px}
.brand .mark{width:22px;height:22px;background:var(--gold)}
.brand small{font-size:10px;font-weight:800;margin-top:10px}
.nav{left:433px;top:29px;font:500 11.5px "Open Sans",sans-serif;color:var(--ink);text-transform:uppercase}
.nav span{position:absolute;white-space:nowrap}
.nav .active{color:var(--gold)}
.flag{top:29px;width:18px;height:12px}

/* hero */
.hero{left:0;top:67px;width:1200px;height:495px;background:radial-gradient(ellipse at 40% 35%,#4a4844 0%,#2a2927 45%,#111 100%)}
.hero-title{left:0;top:262px;width:1200px;text-align:center;font:800 38px/52px "Raleway",sans-serif;color:var(--white);letter-spacing:1px;text-transform:uppercase}
.hero-title em{font-style:normal;color:var(--gold)}
.dots{left:531px;top:503px;display:flex;gap:8px}
.dots i{display:block;width:30px;height:4px;background:var(--white)}
.dots i.on{background:var(--gold)}

/* section headings */
.sec-title{left:0;width:1200px;text-align:center;font:800 28px "Raleway",sans-serif;color:var(--ink);text-transform:uppercase}
.sec-title em{font-style:normal;color:var(--gold)}
.sec-intro{left:300px;width:600px;text-align:center;font-size:11px;line-height:19px;color:var(--text)}

/* services */
.service{width:210px;text-align:center}
.service .icon{width:124px;height:124px;border-radius:50%;background:var(--circle);margin:0 auto;display:flex;align-items:center;justify-content:center}
.service h3{font:600 17px "Raleway",sans-serif;color:var(--ink);margin-top:22px}
.service p{font-size:11px;line-height:19px;margin-top:14px}
.arrow{top:754px}

/* products */
.products{left:0;top:992px;width:1200px;height:474px;background:var(--light);border-top:3px solid var(--gold)}
.tab{left:511px;top:992px;width:212px;height:46px;background:var(--gold);border-radius:0 0 60px 60px;color:var(--white);font:800 26px/44px "Raleway",sans-serif;text-align:center}
.card{top:1082px;width:207px;height:321px;background:var(--white);border:1px solid #e6e6e6;text-align:center}
.card .photo{margin:7px;height:160px;background:linear-gradient(180deg,#e9e9ea,#cfd0d2)}
.card h3{font:600 17px "Raleway",sans-serif;color:var(--ink);margin-top:18px}
.card p{font-size:10.5px;line-height:18px;margin:10px 12px 0}
.btn{display:inline-block;background:var(--gold);color:var(--white);font:600 10px/34px "Open Sans",sans-serif;padding:0 16px;margin-top:14px;text-transform:uppercase}

/* testimonials */
.testi{left:0;top:1466px;width:1200px;height:363px;background:radial-gradient(ellipse at 50% 55%,#3b3b3b 0%,#161616 70%,#0b0b0b 100%)}
.testi-title{top:1540px;color:var(--white)}
.avatar{left:181px;top:1603px;width:114px;height:114px;border-radius:50%;border:4px solid var(--white);background:linear-gradient(160deg,#c9a27e,#8a6a50)}
.quote{left:305px;top:1606px;width:720px;font:italic 11.5px/19px "Open Sans",sans-serif;color:#e6e6e6}
.quote b{color:var(--gold);font:800 22px/0 "Raleway",sans-serif}
.author{left:305px;top:1694px;font:600 12px "Open Sans",sans-serif;color:var(--white)}

/* news */
.news{top:1956px;width:277px}
.news .photo{height:202px}
.news .meta{font-size:11px;color:var(--ink);margin-top:14px}
.news h3{font:600 16px "Raleway",sans-serif;color:var(--gold);margin-top:12px}
.news p{font-size:11px;line-height:19px;margin-top:8px}

/* footer */
.footer{left:0;top:2329px;width:1200px;height:231px;background:var(--dark);border-top:3px solid var(--gold)}
.f-brand{left:162px;top:2385px;font:800 28px/1 "Raleway",sans-serif;color:var(--white);display:flex;align-items:center;gap:8px;letter-spacing:1px}
.f-brand .mark{width:22px;height:22px;background:#bdbdbd}
.f-brand small{font-size:10px;margin-top:10px}
.f-text{left:162px;top:2440px;width:225px;font-size:11px;line-height:18px;color:#ddd}
.f-col h4{font:700 16px "Raleway",sans-serif;color:var(--white);text-transform:uppercase}
.f-col ul{list-style:none;margin-top:10px;font-size:11px;line-height:18px;color:#ddd}
.f-col li svg{vertical-align:-1px;margin-right:10px}
.input{left:796px;width:240px;height:37px;background:var(--white);font:italic 10px/37px "Open Sans",sans-serif;color:#888;padding-left:12px}
.signup{left:958px;top:2476px;width:78px;height:37px;background:var(--gold);color:var(--white);font:700 11px/37px "Open Sans",sans-serif;text-align:center}

/* bottom bar */
.bottom{left:0;top:2560px;width:1200px;height:83px;background:var(--gold)}
.copy{left:162px;top:2584px;font-size:10px;line-height:22px;color:var(--white)}
.social{top:2592px;width:27px;height:27px;border-radius:50%;border:1.5px solid var(--white);display:flex;align-items:center;justify-content:center}
.social i{display:block;width:7px;height:7px;border-radius:50%;background:var(--white)}
</style>
</head>
<body>

<header class="site-header abs">
  <div class="brand abs"><span class="mark"></span>VARNEL<small>Sàrl</small></div>
  <nav class="nav abs">
    <span class="active" style="left:0">Home</span>
    <span style="left:71px">Services</span>
    <span style="left:163px">Products</span>
    <span style="left:263px">Examples</span>
    <span style="left:362px">Download</span>
    <span style="left:471px">Contacts</span>
  </nav>
  <svg class="flag abs" style="left:982px" viewBox="0 0 18 12"><rect width="18" height="12" fill="#22307a"/><rect x="7" width="4" height="12" fill="#fff"/><rect y="4" width="18" height="4" fill="#fff"/><rect x="8" width="2" height="12" fill="#c8202f"/><rect y="5" width="18" height="2" fill="#c8202f"/></svg>
  <svg class="flag abs" style="left:1012px" viewBox="0 0 18 12"><rect width="6" height="12" fill="#1f3f9a"/><rect x="6" width="6" height="12" fill="#fff"/><rect x="12" width="6" height="12" fill="#d42a2f"/></svg>
</header>

<section class="hero abs" role="img" aria-label="Photograph of a precision optical measuring machine in a dark lab"></section>
<h1 class="hero-title abs">Simulation and modeling of<br>complete <em>processes</em></h1>
<div class="dots abs"><i></i><i></i><i class="on"></i><i></i></div>

<h2 class="sec-title abs" style="top:590px">Welcome to <em>Varnel</em></h2>
<p class="sec-intro abs" style="top:636px">Sed ut perspiciatis unde omnis iste natus error sit voluptatem accusantium doloremque laudantium, totam rem aperiam, eaque ipsa quae ab illo inventore veritatis et quasi architecto beate vitae dict a sunt explicabo.</p>

<svg class="arrow abs" style="left:115px" width="14" height="24" viewBox="0 0 14 24"><path d="M12 2 2 12l10 10" fill="none" stroke="#999" stroke-width="2.5"/></svg>
<svg class="arrow abs" style="left:1058px" width="14" height="24" viewBox="0 0 14 24"><path d="M2 2l10 10L2 22" fill="none" stroke="#999" stroke-width="2.5"/></svg>

<div class="service abs" style="left:150px;top:704px">
  <div class="icon"><svg width="60" height="60" viewBox="0 0 60 60" fill="none" stroke="#a99a5c" stroke-width="4" stroke-linecap="round"><rect x="12" y="48" width="26" height="6" fill="#a99a5c" stroke="none"/><path d="M25 48V36l12-16 10 6"/><circle cx="25" cy="36" r="3" fill="#a99a5c"/><circle cx="37" cy="20" r="3" fill="#a99a5c"/><path d="M47 26l4 6M47 26l-2 7"/></svg></div>
  <h3>Simulation</h3><p>Sed ut perspiciatis undloreme tusit voluptatem accusantidloreme umlore au dantium, totam rem aperiam.</p></div>
<div class="service abs" style="left:380px;top:704px">
  <div class="icon"><svg width="60" height="60" viewBox="0 0 60 60" fill="none" stroke="#a99a5c"><circle cx="30" cy="30" r="21" stroke-width="8" stroke-dasharray="6 5.1"/><circle cx="30" cy="30" r="15" stroke-width="4"/><path d="M23 37l12-12 3 3-12 12h-3z" fill="#a99a5c" stroke="none"/></svg></div>
  <h3>Concept &amp; Design</h3><p>Sed ut perspiciatis undloreme tusit voluptatem accusantidloreme umlore au dantium, totam rem aperiam.</p></div>
<div class="service abs" style="left:609px;top:704px">
  <div class="icon"><svg width="60" height="60" viewBox="0 0 60 60"><circle cx="26" cy="16" r="9" fill="#a99a5c"/><path d="M8 52c0-14 8-22 18-22s18 8 18 22z" fill="#a99a5c"/><circle cx="42" cy="42" r="11" fill="#a99a5c" stroke="#e9e9e9" stroke-width="3"/><rect x="36" y="40.5" width="12" height="3" fill="#fff"/></svg></div>
  <h3>Development</h3><p>Sed ut perspiciatis undloreme tusit voluptatem accusantidloreme umlore au dantium, totam rem aperiam.</p></div>
<div class="service abs" style="left:838px;top:704px">
  <div class="icon"><svg width="60" height="60" viewBox="0 0 60 60" fill="#a99a5c"><rect x="18" y="14" width="24" height="22" rx="2"/><path d="M24 14v-5h12v5" fill="none" stroke="#a99a5c" stroke-width="3"/><rect x="8" y="38" width="44" height="6"/><circle cx="16" cy="49" r="4"/><circle cx="44" cy="49" r="4"/><rect x="6" y="20" width="8" height="4"/><rect x="46" y="20" width="8" height="4"/></svg></div>
  <h3>Rapid Prototyping</h3><p>Sed ut perspiciatis undloreme tusit voluptatem accusantidloreme umlore au dantium, totam rem aperiam.</p></div>

<section class="products abs"></section>
<div class="tab abs">PRODUCTS</div>
<div class="card abs" style="left:148px"><div class="photo" role="img" aria-label="Linear encoder product photo"></div><h3>Products 1</h3><p>Sd ut perspiciatis unde omnis iste natus error sit voluptatemusnt.</p><span class="btn">Read more</span></div>
<div class="card abs" style="left:375px"><div class="photo" role="img" aria-label="Linear actuator product photo"></div><h3>Products 2</h3><p>Sd ut perspiciatis unde omnis iste natus error sit voluptatemusnt.</p><span class="btn">Read more</span></div>
<div class="card abs" style="left:603px"><div class="photo" role="img" aria-label="Controller circuit board product photo"></div><h3>Products 3</h3><p>Sd ut perspiciatis unde omnis iste natus error sit voluptatemusnt.</p><span class="btn">Read more</span></div>
<div class="card abs" style="left:830px"><div class="photo" role="img" aria-label="Servo motor product photo"></div><h3>Products 4</h3><p>Sd ut perspiciatis unde omnis iste natus error sit voluptatemusnt.</p><span class="btn">Read more</span></div>

<section class="testi abs" role="img" aria-label="Blurred dark photograph of machinery"></section>
<h2 class="sec-title testi-title abs" style="font-size:26px">Client Testimonials</h2>
<div class="avatar abs" role="img" aria-label="Portrait of the client"></div>
<p class="quote abs"><b>“</b> Sed ut perspiciatis unde omnis iste nater ror sit voptamaccusantium dolorque laudantium, totam rem aperiad persloypiciatis unde omnis iste nater ror sit voluptatem accs antium dolorque laudantium, totam rem aperiamedut perspiciatis unde omnis iste natetis nde omnis iste nater ror sit voptamaccusantium dolorque laudantium, totam rem aperiad perspiciatis unde omnis iste nater ror sit voluptatem accs antium dolorque laudantium, totam rem aperiamedut perspiciatis unde omnis iste nater. <b>”</b></p>
<div class="author abs">Lena Marsh, City Name</div>

<h2 class="sec-title abs" style="top:1848px">Latest <em>News</em></h2>
<p class="sec-intro abs" style="top:1894px">Sed ut perspiciatis unde omnis iste natus error sit voluptatem accusantium doloremque laudantium, totam rem aperiam, eaque ipsa quae ab illo inventore veritatis et quasi architecto beate vitae dict a sunt explicabo.</p>

<article class="news abs" style="left:162px"><div class="photo" role="img" aria-label="Gloved hand soldering a circuit board" style="background:linear-gradient(135deg,#5f7a4f,#c9cbc6)"></div><div class="meta">&#9638; 20 Sep 2016 &nbsp;&nbsp;| &nbsp;&nbsp;&#9633; Comments (05)</div><h3>The Varnel team will be present...</h3><p>Sed ut perspiciatis unde omnis iste natus error sitolu tatem accusantium doloremque laudantium, totamap eriam, eaque ipsa quae ab illo inventore veritati.</p></article>
<article class="news abs" style="left:462px"><div class="photo" role="img" aria-label="Hand holding a copper motor stator" style="background:linear-gradient(135deg,#6d5a48,#c79a6c)"></div><div class="meta">&#9638; 20 Sep 2016 &nbsp;&nbsp;| &nbsp;&nbsp;&#9633; Comments (05)</div><h3>The Varnel team will be present...</h3><p>Sed ut perspiciatis unde omnis iste natus error sitolu tatem accusantium doloremque laudantium, totamap eriam, eaque ipsa quae ab illo inventore veritati.</p></article>
<article class="news abs" style="left:761px"><div class="photo" role="img" aria-label="Open hard disk drive close-up" style="background:linear-gradient(135deg,#9a9ea3,#e4e5e7)"></div><div class="meta">&#9638; 20 Sep 2016 &nbsp;&nbsp;| &nbsp;&nbsp;&#9633; Comments (05)</div><h3>The Varnel team will be present...</h3><p>Sed ut perspiciatis unde omnis iste natus error sitolu tatem accusantium doloremque laudantium, totamap eriam, eaque ipsa quae ab illo inventore veritati.</p></article>

<footer class="footer abs"></footer>
<div class="f-brand abs"><span class="mark"></span>VARNEL<small>Sagl</small></div>
<p class="f-text abs">Sed ut perspici loatis undloreme omnis lss sit oluptat loem accus antiu ndeom niredpa tem acc usassit oluptssiltu ptat loem accus antiu ndeom niremdpt atem acc usa.</p>
<div class="f-col abs" style="left:416px;top:2382px"><h4>Services</h4><ul><li>Simulation and modeling</li><li>Concept and design</li><li>Development</li><li>Rapid prototyping</li><li>Manufacturing and setup</li><li>Customer service</li></ul></div>
<div class="f-col abs" style="left:585px;top:2382px"><h4>Contact Us</h4><ul style="margin-top:14px">
  <li><svg width="8" height="10" viewBox="0 0 8 10"><path d="M4 0a4 4 0 0 1 4 4c0 3-4 6-4 6S0 7 0 4a4 4 0 0 1 4-4z" fill="#ddd"/></svg>Postal address: PO Box 218,</li>
  <li style="padding-left:18px">Cobar dummy adres sire lor</li>
  <li><svg width="9" height="9" viewBox="0 0 9 9"><path d="M1 0h2l1 2-1 1c.6 1.3 1.7 2.4 3 3l1-1 2 1v2C4 8 1 5 1 0z" fill="#ddd"/></svg>Phone: 555-014-2207</li>
  <li><svg width="9" height="9" viewBox="0 0 9 9"><rect y="3" width="9" height="6" fill="#ddd"/><rect x="2" width="5" height="3" fill="#ddd"/></svg>Fax: 555-014-2208</li>
  <li><svg width="9" height="7" viewBox="0 0 9 7"><rect width="9" height="7" fill="#ddd"/><path d="M0 0l4.5 4L9 0" fill="none" stroke="#1c1c1c"/></svg>hello@varnel-example.ch</li>
</ul></div>
<div class="f-col abs" style="left:795px;top:2382px"><h4>Sign up Newsletter</h4><ul style="margin-top:6px"><li>Please sign up here for latest deals</li></ul></div>
<div class="input abs" style="top:2435px">Name:</div>
<div class="input abs" style="top:2476px">Email address</div>
<div class="signup abs">SIGN UP</div>

<div class="bottom abs"></div>
<p class="copy abs">© 2016 varnel. All Copyrights are reserved.<br>Term of Use. Privacy Policy</p>
<span class="social abs" style="left:877px" aria-label="Video channel"><i></i></span>
<span class="social abs" style="left:911px" aria-label="Social network"><i></i></span>
<span class="social abs" style="left:945px" aria-label="Photo network"><i></i></span>
<span class="social abs" style="left:979px" aria-label="Microblog"><i></i></span>
<span class="social abs" style="left:1013px" aria-label="Community page"><i></i></span>

</body>
</html>
```